Veltrano.co - Polar Expeditions Specialists

We need a modern, visually striking business card for Veltrano.co, a company specialized in selling expedition cruises to the most remote regions on Earth, with a focus on the Arctic and Antarctica. The design should instantly communicate that the cardholder is an expert in polar travel. Use clean, premium aesthetics with cool tones like icy blue and white, possibly incorporating polar imagery (ice, glaciers, penguins, etc.)

Attached the logo

Contact Information for Business Card

Feels high-end and trustworthy.. Visually memorable — encourages people to keep it

Colors
0054AA
0677BA
7BADD7
CADEEF
E8F1F8

Requirements
Must have
• ice, glaciers, penguins, montains
Nice to have
• modern, transparente,

```html
<!DOCTYPE html>
<html lang="en">
<head>
<meta charset="utf-8">
<title>Veltrano.co – Business Card</title>
<link href="https://fonts.googleapis.com/css2?family=Poppins:wght@600;700&family=Roboto:wght@400;500&display=swap" rel="stylesheet">
<style>
  :root {
    --brand-blue: #306cab;
    --ice-light: #e8f1f8;
    --ice-mid: #7badd7;
    --ice-pale: #cadeef;
    --band-grey: #5f5f5f;
    --ink: #1f1f1f;
    --muted: #555555;
    --card-white: #f6f6f7;
    --backdrop: #e4e4e4;
    --divider: #b9b9b9;
  }
  * { box-sizing: border-box; margin: 0; padding: 0; }
  html, body { width: 1200px; height: 1040px; overflow: hidden; }
  body { background: var(--backdrop); position: relative; font-family: "Roboto", Arial, sans-serif; }

  .card {
    position: absolute;
    width: 642px;
    height: 367px;
    border-radius: 18px;
    overflow: hidden;
  }
  .card-front { left: 285px; top: 130px; background: var(--card-white); }
  .card-back  { left: 284px; top: 568px; width: 646px; height: 368px; background: var(--brand-blue); }

  .polar-emblem {
    position: absolute;
    border-radius: 50%;
  }
  .card-front .polar-emblem {
    left: 174px; top: 108px; width: 72px; height: 72px;
    background: linear-gradient(180deg, var(--ice-mid), var(--brand-blue));
  }
  .card-back .polar-emblem {
    left: 280px; top: 78px; width: 88px; height: 88px;
    background: linear-gradient(180deg, var(--ice-light), var(--ice-pale));
  }

  .wordmark {
    position: absolute;
    font-family: "Poppins", Arial, sans-serif;
    font-weight: 700;
    text-align: center;
    white-space: nowrap;
    letter-spacing: 0.3px;
    line-height: 1;
  }
  .tagline {
    position: absolute;
    font-family: "Poppins", Arial, sans-serif;
    font-weight: 600;
    text-align: center;
    white-space: nowrap;
    line-height: 1;
  }

  .card-front .wordmark { left: 50px; width: 320px; top: 192px; font-size: 38px; color: var(--brand-blue); }
  .card-front .tagline  { left: 50px; width: 320px; top: 241px; font-size: 12.5px; color: var(--brand-blue); }

  .divider {
    position: absolute; left: 336px; top: 96px; width: 1px; height: 174px;
    background: var(--divider);
  }

  .contact { position: absolute; left: 355px; top: 96px; }
  .contact-name { font-weight: 500; font-size: 25px; color: var(--brand-blue); line-height: 1.1; }
  .contact-role { font-size: 16px; color: var(--muted); margin-top: 0; margin-left: 2px; }
  .contact-address { font-size: 16px; color: var(--ink); margin-top: 10px; line-height: 20px; }
  .contact-lines { list-style: none; margin-top: 10px; font-size: 16px; color: var(--ink); }
  .contact-lines li { display: flex; align-items: center; height: 20px; }
  .contact-lines svg { width: 13px; height: 13px; margin-right: 9px; fill: var(--brand-blue); flex: none; }

  .bottom-band { position: absolute; left: 0; bottom: 0; width: 642px; height: 18px; }

  .card-back .wordmark { left: 0; width: 100%; top: 180px; font-size: 50px; color: #ffffff; }
  .card-back .tagline  { left: 0; width: 100%; top: 242px; font-size: 16px; color: #ffffff; }
</style>
</head>
<body>

<section class="card card-front">
  <div class="polar-emblem" role="img" aria-label="Polar emblem: bear on Antarctic ice under stars"></div>
  <div class="wordmark">Veltrano.co</div>
  <div class="tagline">Polar Expeditions Specialists</div>

  <div class="divider"></div>

  <div class="contact">
    <div class="contact-name">Marcus Hale</div>
    <div class="contact-role">President</div>
    <div class="contact-address">2719 Harbor View Lane<br>Cedar Hollow, NY 11482</div>
    <ul class="contact-lines">
      <li>
        <svg viewBox="0 0 24 24" aria-hidden="true"><path d="M6.6 10.8a15.1 15.1 0 0 0 6.6 6.6l2.2-2.2a1 1 0 0 1 1-.25 11.4 11.4 0 0 0 3.6.57 1 1 0 0 1 1 1V20a1 1 0 0 1-1 1A17 17 0 0 1 3 4a1 1 0 0 1 1-1h3.5a1 1 0 0 1 1 1c0 1.25.2 2.45.57 3.57a1 1 0 0 1-.25 1z"/></svg>
        (612) 5390-7718
      </li>
      <li>
        <svg viewBox="0 0 24 24" aria-hidden="true"><path d="M2 5h20v14H2z M3.5 6.5 12 13l8.5-6.5v1.8L12 14.8 3.5 8.3z" fill-rule="evenodd"/></svg>
        name@veltrano.com
      </li>
      <li>
        <svg viewBox="0 0 24 24" aria-hidden="true"><circle cx="12" cy="12" r="10"/><path d="M8 7c2 0 3 1 2.5 2.5S8 11 9 13s-1 3-2 2.5M15 5.5c-1 1.5 0 2.5 1.5 3s2 2 1 3.5-2 1.5-1.5 3.5" stroke="#f6f6f7" stroke-width="1.6" fill="none"/></svg>
        www.veltrano.com
      </li>
    </ul>
  </div>

  <svg class="bottom-band" viewBox="0 0 642 18" aria-hidden="true">
    <polygon points="0,0 418,0 413,18 0,18" fill="var(--brand-blue)"/>
    <polygon points="423,0 642,0 642,18 418,18" fill="var(--band-grey)"/>
  </svg>
</section>

<section class="card card-back">
  <div class="polar-emblem" role="img" aria-label="Polar emblem: bear on Antarctic ice under stars"></div>
  <div class="wordmark">Veltrano.co</div>
  <div class="tagline">Polar Expeditions Specialists</div>
</section>

</body>
</html>
```